Dental Medical History Form - Content provided

Design a medical history form for a dental practice. Content is provided so all that is needed is the formatting to make it look great and easy to read.

"Patient Information" to include all information contained in top portion of the "Patient Medical History Form" docx file.

"Medical History" should follow the formatting and content of the "Exact Medical History" file as this is what the entry fields look like in our practice software and so we would like it to match.

1st page - Patient info, allergies, medications, antibiotics, joint replacement, pregnancy.

2nd page - Do you have, or have you had, any of the following? . . . . . . .
Updates

Target Market(s)

All ages but must be clear enough for elderly to read. Use as much space as possible to keep font size bigger yet keep to two pages

Industry/Entity Type

Dental

Font styles to use
Sans Serif

Requirements
Must have
• All content provided
• Our logo at the top (file provided)
• Century Gothic Font
• Limit to two pages

```html
<!DOCTYPE html>
<html lang="en">
<head>
<meta charset="utf-8">
<title>Harbourline Dental – Confidential Medical History</title>
<link href="https://fonts.googleapis.com/css2?family=Montserrat:wght@400;600&family=Oswald:wght@500&family=Pathway+Gothic+One&display=swap" rel="stylesheet">
<style>
:root{
  --slate:#36424d;
  --ink:#3a4650;
  --rule:#6e7a84;
  --paper:#ffffff;
  --backdrop:#d9dcdf;
}
*{box-sizing:border-box;margin:0;padding:0}
html,body{width:1200px;height:816px;overflow:hidden}
body{background:var(--backdrop);position:relative;font-family:"Pathway Gothic One",sans-serif;color:var(--ink)}
.page{position:absolute;background:var(--paper);box-shadow:0 1px 4px rgba(0,0,0,.18)}
.page--info{left:30px;top:12px;width:560px;height:792px}
.page--history{left:610px;top:14px;width:558px;height:790px}
.t{position:absolute;font-size:10px;line-height:14px;white-space:nowrap}
.f{position:absolute;height:10px;border:1px solid var(--rule)}
.c{position:absolute;width:11px;height:11px;border:1px solid var(--rule)}
.ln{position:absolute;height:0;border-top:1px solid var(--rule)}
.band{position:absolute;left:0;right:0;height:16px;background:var(--slate);color:#fff;font-size:11px;line-height:16px;text-align:center}
.brand{position:absolute;left:20px;top:34px;font-family:"Montserrat",sans-serif;font-weight:400;font-size:30px;line-height:34px;color:var(--slate);letter-spacing:-.5px}
.practice-address{position:absolute;right:30px;top:34px;text-align:right;font-family:"Oswald",sans-serif;font-weight:500;font-size:8px;line-height:12.5px;color:var(--slate)}
.title{position:absolute;left:0;right:0;top:101px;text-align:center;font-family:"Montserrat",sans-serif;font-weight:600;font-size:17px;letter-spacing:2px;color:var(--slate)}
.foot-band{position:absolute;left:0;right:0;bottom:0;height:8px;background:var(--slate)}
.foot-tab{position:absolute;left:214px;width:132px;height:20px;bottom:0;background:var(--slate);border-radius:8px 8px 0 0;color:#fff;font-size:10.5px;line-height:22px;text-align:center}
.history-head{position:absolute;left:0;right:0;top:0;height:22px;background:var(--slate);color:#fff;font-family:"Oswald",sans-serif;font-weight:500;font-size:11px;line-height:22px;text-align:center}
.h{position:absolute;font-family:"Oswald",sans-serif;font-weight:500;font-size:10px;line-height:14px;color:var(--slate);white-space:nowrap}
.sig{font-family:"Oswald",sans-serif;font-weight:500}
.thanks{position:absolute;left:0;right:0;text-align:center;font-size:6.5px;line-height:10px}
</style>
</head>
<body>

<section class="page page--info" aria-label="Patient information">
  <div class="brand">harbourline dental</div>
  <address class="practice-address">3.04/118 Seaview Road,<br>Lakeside NSW 2260<br>(02) 40 512 318</address>
  <h1 class="title">CONFIDENTIAL MEDICAL HISTORY</h1>
  <div class="band" style="top:121px"></div>

  <span class="t" style="left:26px;top:149px">Name:</span>
  <span class="f" style="left:60px;top:151px;width:44px"></span>
  <span class="f" style="left:110px;top:151px;width:136px"></span>
  <span class="f" style="left:254px;top:151px;width:136px"></span>
  <span class="f" style="left:398px;top:151px;width:136px"></span>

  <span class="t" style="left:26px;top:175px">Address:</span>
  <span class="f" style="left:60px;top:177px;width:474px"></span>

  <span class="t" style="left:26px;top:202px">Email Address:</span>
  <span class="f" style="left:86px;top:204px;width:303px"></span>
  <span class="t" style="left:400px;top:202px">DOB:</span>
  <span class="c" style="left:426px;top:203px"></span><span class="c" style="left:438px;top:203px"></span>
  <span class="c" style="left:455px;top:203px"></span><span class="c" style="left:468px;top:203px"></span>
  <span class="c" style="left:485px;top:203px"></span><span class="c" style="left:498px;top:203px"></span>
  <span class="c" style="left:510px;top:203px"></span><span class="c" style="left:523px;top:203px"></span>

  <span class="t" style="left:26px;top:227px">Phone Number(s): Mobile</span>
  <span class="f" style="left:124px;top:229px;width:134px"></span>
  <span class="t" style="left:263px;top:227px">Work</span>
  <span class="f" style="left:285px;top:229px;width:109px"></span>
  <span class="t" style="left:399px;top:227px">Home</span>
  <span class="f" style="left:425px;top:229px;width:109px"></span>

  <span class="t" style="left:26px;top:254px">Emergency Contact Person: Name:</span>
  <span class="f" style="left:149px;top:256px;width:109px"></span>
  <span class="t" style="left:263px;top:254px">Relationship:</span>
  <span class="f" style="left:311px;top:256px;width:79px"></span>
  <span class="t" style="left:394px;top:254px">Phone number:</span>
  <span class="f" style="left:450px;top:256px;width:84px"></span>

  <span class="t" style="left:26px;top:280px">General Practitioner Name:</span>
  <span class="f" style="left:126px;top:282px;width:239px"></span>
  <span class="t" style="left:372px;top:280px">Phone:</span>
  <span class="f" style="left:402px;top:282px;width:132px"></span>

  <span class="t" style="left:26px;top:307px">General Practitioner Address:</span>
  <span class="f" style="left:133px;top:309px;width:401px"></span>

  <span class="t" style="left:26px;top:332px">Do you have dental health fund cover?</span>
  <span class="t" style="left:173px;top:332px">Yes</span><span class="c" style="left:189px;top:333px"></span>
  <span class="t" style="left:205px;top:332px">or</span><span class="c" style="left:218px;top:333px"></span>
  <span class="t" style="left:236px;top:332px">No</span>
  <span class="t" style="left:254px;top:332px">If so, what is the name of the fund?</span>
  <span class="f" style="left:386px;top:334px;width:148px"></span>

  <span class="t" style="left:26px;top:359px">Fund Number?</span>
  <span class="f" style="left:80px;top:361px;width:200px"></span>
  <span class="t" style="left:288px;top:359px">Priority Number on card:</span>
  <span class="c" style="left:382px;top:360px"></span><span class="t" style="left:397px;top:359px">1</span>
  <span class="c" style="left:408px;top:360px"></span><span class="t" style="left:423px;top:359px">2</span>
  <span class="c" style="left:433px;top:360px"></span><span class="t" style="left:448px;top:359px">3</span>
  <span class="c" style="left:458px;top:360px"></span><span class="t" style="left:473px;top:359px">4</span>
  <span class="c" style="left:484px;top:360px"></span><span class="t" style="left:499px;top:359px">5</span>
  <span class="c" style="left:511px;top:360px"></span><span class="t" style="left:526px;top:359px">6</span>

  <span class="t" style="left:26px;top:385px">Occupation:</span>
  <span class="f" style="left:71px;top:387px;width:209px"></span>
  <span class="t" style="left:287px;top:385px">Referred by:</span>
  <span class="f" style="left:338px;top:387px;width:196px"></span>

  <div class="band" style="top:410px">Please indicate if you are allergic to any of the following?</div>
  <span class="t" style="left:26px;top:444px">Aspirin</span><span class="c" style="left:61px;top:445px"></span>
  <span class="t" style="left:85px;top:444px">Codeine</span><span class="c" style="left:122px;top:445px"></span>
  <span class="t" style="left:146px;top:444px">Penicillin</span><span class="c" style="left:189px;top:445px"></span>
  <span class="t" style="left:212px;top:444px">Sulfites</span><span class="c" style="left:248px;top:445px"></span>
  <span class="t" style="left:272px;top:444px">Latex</span><span class="c" style="left:301px;top:445px"></span>
  <span class="t" style="left:324px;top:444px">Local Anaesthetic</span><span class="c" style="left:395px;top:445px"></span>
  <span class="t" style="left:419px;top:444px">Lactose</span><span class="c" style="left:456px;top:445px"></span>
  <span class="t" style="left:479px;top:444px">Nickel</span><span class="c" style="left:510px;top:445px"></span>
  <span class="t" style="left:26px;top:471px">Other:</span>
  <span class="f" style="left:54px;top:473px;width:480px"></span>

  <div class="band" style="top:502px">Are you currently taking, or have ever taken, any of the following medication?</div>
  <span class="t" style="left:22px;top:535px">Asthma inhaler</span><span class="c" style="left:86px;top:536px"></span>
  <span class="t" style="left:110px;top:535px">Anti-epileptics</span><span class="c" style="left:171px;top:536px"></span>
  <span class="t" style="left:195px;top:535px">Anti-depressants</span><span class="c" style="left:266px;top:536px"></span>
  <span class="t" style="left:288px;top:535px">Blood Pressure</span><span class="c" style="left:350px;top:536px"></span>
  <span class="t" style="left:374px;top:535px">Blood Thinners</span><span class="c" style="left:435px;top:536px"></span>
  <span class="t" style="left:458px;top:535px">Bisphosphonates</span><span class="c" style="left:526px;top:536px"></span>
  <span class="t" style="left:22px;top:561px">Chemotherapy</span><span class="c" style="left:86px;top:562px"></span>
  <span class="t" style="left:107px;top:561px">Insulin</span><span class="c" style="left:142px;top:562px"></span>
  <span class="t" style="left:166px;top:561px">Immunosuppressants</span><span class="c" style="left:251px;top:562px"></span>
  <span class="t" style="left:274px;top:561px">Steroids</span><span class="c" style="left:311px;top:562px"></span>
  <span class="t" style="left:335px;top:561px">Other</span><span class="c" style="left:365px;top:562px"></span>

  <div class="band" style="top:592px">Please specify medication name, dose, and frequency where possible:</div>
  <span class="ln" style="left:19px;top:630px;width:170px"></span><span class="ln" style="left:195px;top:630px;width:170px"></span><span class="ln" style="left:371px;top:630px;width:170px"></span>
  <span class="ln" style="left:19px;top:654px;width:170px"></span><span class="ln" style="left:195px;top:654px;width:170px"></span><span class="ln" style="left:371px;top:654px;width:170px"></span>
  <span class="ln" style="left:19px;top:678px;width:170px"></span><span class="ln" style="left:195px;top:678px;width:170px"></span><span class="ln" style="left:371px;top:678px;width:170px"></span>

  <span class="t" style="left:19px;top:695px">Do you require antibiotic cover?</span>
  <span class="t" style="left:162px;top:695px">Yes</span><span class="c" style="left:182px;top:696px"></span>
  <span class="t" style="left:206px;top:695px">No</span><span class="c" style="left:222px;top:696px"></span>
  <span class="t" style="left:19px;top:718px">Have you had a joint replacement?</span>
  <span class="t" style="left:162px;top:718px">Yes</span><span class="c" style="left:182px;top:719px"></span>
  <span class="t" style="left:206px;top:718px">No</span><span class="c" style="left:222px;top:719px"></span>
  <span class="t" style="left:19px;top:741px">Women: Are you pregnant?</span>
  <span class="t" style="left:162px;top:741px">Yes</span><span class="c" style="left:182px;top:742px"></span>
  <span class="t" style="left:206px;top:741px">No</span><span class="c" style="left:222px;top:742px"></span>
  <span class="t" style="left:246px;top:741px">Possible</span><span class="c" style="left:283px;top:742px"></span>
  <span class="t" style="left:305px;top:741px">How Many Weeks?</span><span class="c" style="left:376px;top:742px"></span><span class="c" style="left:393px;top:742px"></span>

  <div class="foot-band"></div>
  <div class="foot-tab">Please Turn Over</div>
</section>

<section class="page page--history" aria-label="Medical history">
  <div class="history-head">Do you have, or have you had, any of the following?</div>

  <!-- left column -->
  <span class="h" style="left:35px;top:35px">Dental</span>
  <span class="t" style="left:35px;top:52px">Acid Reflux</span>
  <span class="t" style="left:35px;top:70px">Bad Breath/Taste</span>
  <span class="t" style="left:35px;top:88px">Bleeding/Swollen/Sore Gums</span>
  <span class="t" style="left:35px;top:106px">Blisters/Ulcers in Mouth</span>
  <span class="t" style="left:35px;top:124px">Broken tooth/filling</span>
  <span class="t" style="left:35px;top:141px">Burning tongue</span>
  <span class="t" style="left:35px;top:159px">Dry mouth</span>
  <span class="t" style="left:35px;top:177px">Food collection between teeth</span>
  <span class="t" style="left:35px;top:195px">Grinding/clenching teeth (day/night)</span>
  <span class="t" style="left:35px;top:213px">Loose teeth</span>
  <span class="t" style="left:35px;top:231px">Crooked teeth</span>
  <span class="t" style="left:35px;top:249px">Discoloured teeth</span>
  <span class="t" style="left:35px;top:267px">Sensitivity to Hot/Cold</span>
  <span class="t" style="left:35px;top:284px">Tooth pain when chewing</span>
  <span class="t" style="left:35px;top:302px">Jaw pain/Fracture</span>
  <span class="t" style="left:35px;top:320px">Orthodontic treatment/history</span>
  <span class="t" style="left:35px;top:338px">Oral Cancer</span>
  <span class="h" style="left:35px;top:356px">Diet/Lifestyle</span>
  <span class="t" style="left:35px;top:374px">Drink more than one glass alcohol per day</span>
  <span class="t" style="left:35px;top:392px">Smoking</span>
  <span class="t" style="left:35px;top:410px">Carbonated drinks</span>
  <span class="t" style="left:35px;top:427px">Sugary foods</span>
  <span class="h" style="left:35px;top:445px">Blood</span>
  <span class="t" style="left:35px;top:463px">Anaemia</span>
  <span class="t" style="left:35px;top:481px">Blood clots</span>
  <span class="t" style="left:35px;top:499px">Leukemia</span>
  <span class="t" style="left:35px;top:517px">Low platelets</span>
  <span class="h" style="left:35px;top:535px">Chest</span>
  <span class="t" style="left:35px;top:553px">Bronchitis</span>
  <span class="t" style="left:37px;top:570px">Emphysema</span>
  <span class="t" style="left:35px;top:588px">Pneumonia</span>
  <span class="h" style="left:35px;top:606px">Infectious Disease</span>
  <span class="t" style="left:35px;top:624px">Hepatitis A,B,C,D</span>
  <span class="t" style="left:35px;top:642px">HIV/AIDS</span>
  <span class="t" style="left:35px;top:660px">Shingles</span>
  <span class="t" style="left:35px;top:678px">Tuberculosis</span>

  <svg class="yes-no" width="558" height="700" style="position:absolute;left:0;top:0" aria-hidden="true">
    <defs>
      <g id="yn-a">
        <text x="190" y="10" font-family="Pathway Gothic One, sans-serif" font-size="10" fill="#3a4650">Yes</text>
        <rect x="206.5" y="0.5" width="11" height="11" fill="none" stroke="#6e7a84"/>
        <text x="227" y="10" font-family="Pathway Gothic One, sans-serif" font-size="10" fill="#3a4650">No</text>
        <rect x="243.5" y="0.5" width="11" height="11" fill="none" stroke="#6e7a84"/>
      </g>
      <g id="yn-b">
        <text x="458" y="10" font-family="Pathway Gothic One, sans-serif" font-size="10" fill="#3a4650">Yes</text>
        <rect x="475.5" y="0.5" width="11" height="11" fill="none" stroke="#6e7a84"/>
        <text x="495" y="10" font-family="Pathway Gothic One, sans-serif" font-size="10" fill="#3a4650">No</text>
        <rect x="511.5" y="0.5" width="11" height="11" fill="none" stroke="#6e7a84"/>
      </g>
    </defs>
    <use href="#yn-a" y="53"/><use href="#yn-a" y="71"/><use href="#yn-a" y="89"/><use href="#yn-a" y="107"/>
    <use href="#yn-a" y="125"/><use href="#yn-a" y="142"/><use href="#yn-a" y="160"/><use href="#yn-a" y="178"/>
    <use href="#yn-a" y="196"/><use href="#yn-a" y="214"/><use href="#yn-a" y="232"/><use href="#yn-a" y="250"/>
    <use href="#yn-a" y="268"/><use href="#yn-a" y="285"/><use href="#yn-a" y="303"/><use href="#yn-a" y="321"/>
    <use href="#yn-a" y="339"/>
    <use href="#yn-a" y="375"/><use href="#yn-a" y="393"/><use href="#yn-a" y="411"/><use href="#yn-a" y="428"/>
    <use href="#yn-a" y="464"/><use href="#yn-a" y="482"/><use href="#yn-a" y="500"/><use href="#yn-a" y="518"/>
    <use href="#yn-a" y="554"/><use href="#yn-a" y="571"/><use href="#yn-a" y="589"/>
    <use href="#yn-a" y="625"/><use href="#yn-a" y="643"/><use href="#yn-a" y="661"/><use href="#yn-a" y="679"/>

    <use href="#yn-b" y="53"/><use href="#yn-b" y="71"/><use href="#yn-b" y="89"/><use href="#yn-b" y="107"/>
    <use href="#yn-b" y="125"/><use href="#yn-b" y="142"/><use href="#yn-b" y="160"/><use href="#yn-b" y="178"/>
    <use href="#yn-b" y="196"/><use href="#yn-b" y="214"/><use href="#yn-b" y="232"/><use href="#yn-b" y="250"/>
    <use href="#yn-b" y="285"/><use href="#yn-b" y="303"/><use href="#yn-b" y="321"/><use href="#yn-b" y="339"/>
    <use href="#yn-b" y="357"/><use href="#yn-b" y="375"/><use href="#yn-b" y="393"/><use href="#yn-b" y="411"/>
    <use href="#yn-b" y="428"/><use href="#yn-b" y="446"/><use href="#yn-b" y="464"/><use href="#yn-b" y="482"/>
    <use href="#yn-b" y="500"/><use href="#yn-b" y="518"/><use href="#yn-b" y="536"/>
  </svg>

  <!-- right column -->
  <span class="h" style="left:306px;top:35px">Heart</span>
  <span class="t" style="left:306px;top:52px">Angina</span>
  <span class="t" style="left:306px;top:70px">Atrial Fibrillation</span>
  <span class="t" style="left:306px;top:88px">Blood Pressure (High/Low)</span>
  <span class="t" style="left:306px;top:106px">Congenital Heart Disease</span>
  <span class="t" style="left:306px;top:124px">Heart attack</span>
  <span class="t" style="left:306px;top:141px">Heart murmur</span>
  <span class="t" style="left:306px;top:159px">Heart surgery</span>
  <span class="t" style="left:306px;top:177px">Heart valve replacement</span>
  <span class="t" style="left:306px;top:195px">Infective endocarditis</span>
  <span class="t" style="left:306px;top:213px">Rheumatic Heart Disease</span>
  <span class="t" style="left:306px;top:231px">Pacemaker</span>
  <span class="t" style="left:306px;top:249px">Stent</span>
  <span class="h" style="left:306px;top:267px">Other</span>
  <span class="t" style="left:306px;top:284px">Anxiety/PTSD</span>
  <span class="t" style="left:306px;top:302px">Arthritis</span>
  <span class="t" style="left:306px;top:320px">Alzheimer's</span>
  <span class="t" style="left:306px;top:338px">Angina</span>
  <span class="t" style="left:306px;top:356px">Asthma</span>
  <span class="t" style="left:306px;top:374px">Anaphylaxis</span>
  <span class="t" style="left:306px;top:392px">Auto-immune disease/Depression</span>
  <span class="t" style="left:306px;top:410px">Diabetes</span>
  <span class="t" style="left:306px;top:427px">Epilepsy</span>
  <span class="t" style="left:306px;top:445px">Kidney Disease</span>
  <span class="t" style="left:306px;top:463px">Liver Disease</span>
  <span class="t" style="left:306px;top:481px">Osteoporosis</span>
  <span class="t" style="left:306px;top:499px">Radiation to Head/Neck/Snoring</span>
  <span class="t" style="left:306px;top:517px">Sleep apnea</span>
  <span class="t" style="left:306px;top:535px">Stroke</span>
  <span class="h" style="left:306px;top:553px">Please list any other conditions we should be aware of:</span>
  <span class="f" style="left:305px;top:573px;width:218px;height:13px"></span>
  <span class="f" style="left:305px;top:594px;width:218px;height:13px"></span>
  <span class="f" style="left:305px;top:614px;width:218px;height:13px"></span>
  <span class="f" style="left:305px;top:635px;width:218px;height:13px"></span>
  <span class="f" style="left:305px;top:656px;width:218px;height:13px"></span>
  <span class="f" style="left:305px;top:677px;width:218px;height:13px"></span>

  <span class="t sig" style="left:30px;top:719px">Signature</span>
  <span class="ln" style="left:74px;top:731px;width:125px"></span>
  <span class="t sig" style="left:380px;top:721px">Date</span>
  <span class="ln" style="left:404px;top:733px;width:128px"></span>

  <p class="thanks" style="top:744px">Thank you for the time to complete your medical history form.</p>
  <p class="thanks" style="top:754px">Oral health is linked to overall health and this comprehensive questionnaire will help us to provide you with optimal and safe care.</p>

  <div class="foot-band"></div>
  <div class="foot-tab" style="height:12px"></div>
</section>

</body>
</html>
```